Maplecrest Disability - Social Security Disability Attorneys

Our company is expanding to attract clients nationwide for our social security disability practice. We have a logo, but I am looking for a creative and elegant letterhead that projects an image of being technologically advanced but still professional enough for the legal field. I am looking for the "wow factor" combined with this is still professional enough for a law practice.

Requesting letterhead and business card design
Updates

Had to update and change the logo. The previous logo had a typo. Please send updates with the new logo for consideration. The letterhead and business cards should be professional enough to be used for a law firm. Thanks.

Industry/Entity Type

Law Practice, Law Firm, Healthcare Industry, Government

Colors

Designer to choose colors to be used in the design.

Requirements
Nice to have
• **Please create a vertical design for the business card**

```html
<!DOCTYPE html>
<html lang="en">
<head>
<meta charset="utf-8">
<title>Maplecrest Disability – Stationery</title>
<link href="https://fonts.googleapis.com/css2?family=Lato:wght@400;700&family=Montserrat:wght@400;500;700&family=Allura&display=swap" rel="stylesheet">
<style>
  :root {
    --backdrop: #b9b9bb;
    --paper: #ffffff;
    --blue: #4469d6;
    --card-blue: #5672bf;
    --orange: #f17f29;
    --ink: #222222;
    --logo-blue: #4a63c4;
  }
  * { margin: 0; padding: 0; box-sizing: border-box; }
  html, body { width: 1200px; height: 848px; overflow: hidden; }
  body { background: var(--backdrop); position: relative; font-family: 'Lato', sans-serif; color: var(--ink); }

  .sheet, .card { position: absolute; background: var(--paper); box-shadow: 0 3px 8px rgba(0,0,0,.25); overflow: hidden; }
  .trim { position: absolute; left: 0; top: 0; width: 100%; height: 100%; }

  /* Letterhead */
  .letterhead { left: 151px; top: 118px; width: 455px; height: 623px; }
  .brand-name { position: absolute; font-family: 'Lato', sans-serif; font-weight: 400; color: var(--logo-blue); letter-spacing: .12em; text-transform: uppercase; white-space: nowrap; }
  .brand-dot { display: inline-block; border-radius: 50%; background: var(--orange); vertical-align: middle; }
  .letterhead .brand-name { left: 25px; top: 56px; font-size: 11px; }
  .letterhead .brand-dot { width: 7px; height: 7px; margin-right: 6px; margin-top: -2px; }
  .letterhead-contact { position: absolute; left: 321px; top: 36px; border-left: 1px solid var(--orange); padding-left: 6px; font-size: 7px; line-height: 10.4px; }
  .letterhead-contact .row { display: flex; align-items: center; gap: 5px; }
  .letterhead-contact .address { margin-bottom: 2px; }
  .letterhead-contact svg { width: 7px; height: 7px; }

  .letter { position: absolute; left: 25px; top: 147px; width: 405px; font-size: 8.3px; line-height: 9.8px; }
  .letter p { margin-bottom: 9.8px; text-align: justify; }
  .letter .date, .letter .recipient { font-size: 9px; line-height: 10.4px; text-align: left; }
  .letter .date { margin-bottom: 11px; }
  .letter .salutation { font-size: 10.5px; font-weight: 700; margin: 2px 0 9px; }
  .letter .closing { margin-top: 20px; text-align: left; }
  .signature { font-family: 'Allura', cursive; font-size: 24px; line-height: 30px; margin-top: 6px; }

  /* Business cards */
  .card { top: 234px; width: 213px; height: 373px; }
  .card-front { left: 627px; font-family: 'Montserrat', sans-serif; text-align: center; }
  .card-front .brand-name { left: 0; right: 0; top: 77px; font-size: 12px; }
  .card-front .brand-dot { width: 8px; height: 8px; margin-right: 6px; margin-top: -2px; }
  .holder-name { position: absolute; left: 0; right: 0; top: 133px; color: var(--orange); font-weight: 700; font-size: 12.5px; }
  .holder-role { position: absolute; left: 0; right: 0; top: 152px; font-size: 9.5px; display: flex; align-items: center; justify-content: center; gap: 3px; }
  .holder-role::before, .holder-role::after { content: ""; width: 28px; height: 1px; background: var(--orange); }
  .card-address { position: absolute; left: 0; right: 0; top: 191px; font-size: 8.6px; line-height: 12.4px; font-weight: 500; }
  .card-icons { position: absolute; left: 0; right: 0; top: 233px; display: flex; justify-content: center; gap: 17px; }
  .card-icons svg { width: 9px; height: 9px; }
  .card-lines { position: absolute; left: 0; right: 0; top: 260px; font-size: 8.6px; line-height: 14px; font-weight: 500; }

  .card-back { left: 864px; background: var(--card-blue); font-family: 'Montserrat', sans-serif; text-align: center; color: #fff; }
  .card-back .brand-name { left: 0; right: 0; top: 86px; font-size: 11.5px; color: #fff; }
  .card-back .brand-dot { width: 8px; height: 8px; margin-right: 6px; margin-top: -2px; background: #fff; }
  .card-sectors { position: absolute; left: 0; right: 0; top: 317px; font-size: 8.4px; line-height: 12.5px; }
</style>
</head>
<body>

<section class="sheet letterhead">
  <svg class="trim" viewBox="0 0 871 1193" preserveAspectRatio="none" aria-hidden="true">
    <polygon fill="var(--blue)" points="0,0 871,0 871,27 290,27 263,53 0,53"/>
    <polygon fill="var(--blue)" points="290,37 511,37 511,50 277,50"/>
    <rect fill="var(--orange)" x="518" y="37" width="158" height="13"/>
    <rect fill="var(--blue)" x="683" y="37" width="188" height="13"/>
    <polygon fill="var(--blue)" points="578,1135 871,1135 871,1193 0,1193 0,1163 550,1163"/>
    <rect fill="var(--blue)" x="0" y="1138" width="156" height="13"/>
    <rect fill="var(--orange)" x="163" y="1138" width="157" height="13"/>
    <polygon fill="var(--blue)" points="327,1138 560,1138 547,1151 327,1151"/>
  </svg>

  <div class="brand-name"><span class="brand-dot"></span>Maplecrest Disability</div>

  <div class="letterhead-contact">
    <div class="address">Suite 5, Level 18, Ashby<br>Street Sydney NSW 2000</div>
    <div class="row"><svg viewBox="0 0 10 10"><path fill="var(--orange)" d="M2 1l2 2-1 1.2c.6 1.2 1.5 2.1 2.8 2.8L7 6l2 2-1.3 1.3C4.5 9 1 5.5.7 2.3z"/></svg>555-014-2290</div>
    <div class="row"><svg viewBox="0 0 10 10"><rect fill="var(--orange)" x="0" y="2" width="10" height="6.5"/><path d="M0 2l5 3.5L10 2" stroke="#fff" stroke-width=".8" fill="none"/></svg>info@maplecrestdisability.com</div>
    <div class="row"><svg viewBox="0 0 10 10"><circle fill="var(--orange)" cx="5" cy="5" r="4.7"/><path d="M.5 5h9M5 .3c-2 2.6-2 6.8 0 9.4M5 .3c2 2.6 2 6.8 0 9.4" stroke="#fff" stroke-width=".6" fill="none"/></svg>www.maplecrestdisability.com</div>
  </div>

  <article class="letter">
    <p class="date">January-03-2020</p>
    <p class="recipient">Mr, Peter Lane<br>President</p>
    <p class="recipient">Northfield Corporation<br>123 Street Name, Suite# 10<br>City, State, 120023</p>
    <p class="salutation">Dear Mr, Peter</p>
    <p>Lorem ipsum dolor sit amet, consectetur adipisicing elit, sed do eiusmod tempor incididunt ut labore et dolore magna aliqua. Ut enim ad minim veniam, quis nostrud exercitation ullamco laboris nisi ut aliquip ex ea commodo consequat. Duis aute irure dolor in reprehenderit in voluptate velit esse cillum dolore eu fugiat nulla pariatur.</p>
    <p>Lorem ipsum dolor sit amet, consectetur adipisicing elit, sed do eiusmod tempor incididunt ut labore et dolore magna aliqua. Ut enim ad minim veniam, quis nostrud exercitation ullamco laboris nisi ut aliquip ex ea commodo consequat. Duis aute irure dolor in reprehenderit in voluptate velit esse cillum dolore eu fugiat nulla pariatur.</p>
    <p>Lorem ipsum dolor sit amet, consectetur adipisicing elit, sed do eiusmod tempor incididunt ut labore et dolore magna aliqua. Ut enim ad minim veniam, quis nostrud exercitation ullamco laboris nisi ut aliquip ex ea commodo consequat.</p>
    <p>Excepteur sint occaecat cupidatat non proident, sunt in culpa qui officia deserunt mollit anim id est laborum. re et dolore magnam aliquam quaerat voluptatem.</p>
    <p class="closing">Regards</p>
    <div class="signature">Daniel Reed</div>
  </article>
</section>

<section class="card card-front">
  <svg class="trim" viewBox="0 0 408 713" preserveAspectRatio="none" aria-hidden="true">
    <polygon fill="var(--card-blue)" points="0,0 408,0 408,14 140,14 128,28 0,28"/>
    <polygon fill="var(--card-blue)" points="140,20 246,20 246,27 134,27"/>
    <rect fill="var(--orange)" x="249" y="20" width="74" height="7"/>
    <rect fill="var(--card-blue)" x="326" y="20" width="82" height="7"/>
    <polygon fill="var(--card-blue)" points="270,684 408,684 408,713 0,713 0,697 258,697"/>
    <rect fill="var(--card-blue)" x="0" y="686" width="74" height="7"/>
    <rect fill="var(--orange)" x="77" y="686" width="74" height="7"/>
    <polygon fill="var(--card-blue)" points="154,686 262,686 255,693 154,693"/>
  </svg>
  <div class="brand-name"><span class="brand-dot"></span>Maplecrest Disability</div>
  <div class="holder-name">ALAN WHITMORE</div>
  <div class="holder-role">Co-Founder</div>
  <div class="card-address">Suite 5, Level 18, Ashby<br>Street Sydney NSW 2000</div>
  <div class="card-icons">
    <svg viewBox="0 0 10 10"><path fill="var(--orange)" d="M2 1l2 2-1 1.2c.6 1.2 1.5 2.1 2.8 2.8L7 6l2 2-1.3 1.3C4.5 9 1 5.5.7 2.3z"/></svg>
    <svg viewBox="0 0 10 10"><rect fill="var(--orange)" x="0" y="2" width="10" height="6.5"/><path d="M0 2l5 3.5L10 2" stroke="#fff" stroke-width=".8" fill="none"/></svg>
    <svg viewBox="0 0 10 10"><circle fill="var(--orange)" cx="5" cy="5" r="4.7"/><path d="M.5 5h9M5 .3c-2 2.6-2 6.8 0 9.4M5 .3c2 2.6 2 6.8 0 9.4" stroke="#fff" stroke-width=".6" fill="none"/></svg>
  </div>
  <div class="card-lines">555-014-2290<br>info@maplecrestdisability.com<br>www.maplecrestdisability.com</div>
</section>

<section class="card card-back">
  <div class="brand-name"><span class="brand-dot"></span>Maplecrest Disability</div>
  <div class="card-sectors">Law Practice, Law Firm,<br>Healthcare Industry, Government</div>
</section>

</body>
</html>
```